Fun, Clean Business Card For Family Focused Travel Agency

I need a business card using specific colors and fonts as in the uploaded files. Ideally, I would like a large image of the logo on the back and all the contact info on the front. Maybe the stars/dots somewhere in a flowy form.

I do want it the contact information to be clear and easy to read. I don't want it to look too busy. Maybe even a bit minimalist.

I plan or ordering the ROUNDED CORNER business cards from Cardwell Press, so please consider that in your design.

Target Market(s)

Families with children, couples, groups of friends

Contact Information for Business Card

Marla Quint, Owner
Marla@TumbleTrips.example
Cell Phone Number 555-218-4603
Office Phone Number 555-647-1925
Specializing in Glimmerland destinations, Pelican Bay Fun Park, Cruises and All-Inclusive Vacations.

Nice but not required:
www.TumbleTrips.example
(plain square, no mark), (omitted), (omitted) icons with username: TumbleTrips

Font styles to use
Sans Serif

Requirements
Must have
• Please try to use the colors from the logo as much as possible. I understand lighter shades/colors may be needed for some things.
Should not have
• NO SERIF FONTS. That is really the only thing I do not want at all

```html
<!DOCTYPE html>
<html lang="en">
<head>
<meta charset="UTF-8">
<title>Tumble Trips – Business Card</title>
<link rel="stylesheet" href="https://fonts.googleapis.com/css2?family=PT+Sans:wght@400;700&family=Kaushan+Script&display=swap">
<style>
  :root{
    --stage:#e4e6e9;
    --navy:#161629;
    --ink:#1d1d2b;
    --paper:#ffffff;
    --blue:#2a9bd6;
    --teal:#16b39a;
    --green:#8cc63f;
    --yellow:#d9b22a;
    --orange:#e8772a;
    --card-w:600px;
    --card-h:343px;
    --band-h:18px;
  }
  *{box-sizing:border-box;margin:0;padding:0}
  html,body{width:1200px;height:800px;overflow:hidden}
  body{
    background:var(--stage);
    font-family:"PT Sans",sans-serif;
    color:var(--ink);
    display:flex;flex-direction:column;align-items:center;justify-content:center;gap:34px;
  }
  .card{
    position:relative;width:var(--card-w);height:var(--card-h);
    border-radius:22px;overflow:hidden;
    box-shadow:0 10px 26px rgba(0,0,0,.18);
  }
  .color-band{position:absolute;left:0;right:0;bottom:0;height:var(--band-h);display:flex}
  .color-band span{flex:1}
  .band-blue{background:var(--blue)} .band-teal{background:var(--teal)}
  .band-green{background:var(--green)} .band-yellow{background:var(--yellow)}
  .band-orange{background:var(--orange)}

  /* back */
  .card-back{background:var(--navy);display:flex;align-items:center;justify-content:center;padding-bottom:var(--band-h)}
  .wordmark{display:flex;align-items:center;gap:14px;font-weight:700;font-size:64px;color:var(--paper);letter-spacing:.5px}
  .wordmark-dot{width:26px;height:26px;border-radius:50%;background:var(--teal)}

  /* front */
  .card-front{background:var(--paper)}
  .front-wordmark{position:absolute;left:34px;top:36px;font-size:40px;color:var(--ink);gap:10px}
  .front-wordmark .wordmark-dot{width:18px;height:18px}
  .specialties{position:absolute;left:34px;top:150px;font-size:17px;line-height:1.3}
  .specialties-title{color:var(--teal);font-size:18px}
  .specialties ul{list-style:none}
  .specialties li{display:flex;align-items:center;gap:7px}
  .specialties li::before{content:"";width:7px;height:7px;background:var(--bullet)}
  .agent{position:absolute;left:340px;top:84px}
  .agent-name{font-family:"Kaushan Script",cursive;color:var(--teal);font-size:34px;line-height:1}
  .agent-role{font-size:15px;letter-spacing:.5px;margin-top:2px}
  .contacts{position:absolute;left:340px;top:176px;list-style:none;font-size:17px;line-height:1.35}
  .contacts li{display:flex;align-items:center;gap:8px}
  .contacts svg{width:15px;height:15px;flex:none}
  .social{position:absolute;left:340px;top:282px;display:flex;align-items:center;gap:10px;font-size:18px}
  .social-mark{width:16px;height:16px;background:var(--teal);border-radius:3px}
</style>
</head>
<body>

<section class="card card-back" aria-label="Card back">
  <div class="wordmark"><span class="wordmark-dot"></span>TumbleTrips</div>
  <div class="color-band">
    <span class="band-orange"></span><span class="band-yellow"></span><span class="band-green"></span><span class="band-teal"></span><span class="band-blue"></span>
  </div>
</section>

<section class="card card-front" aria-label="Card front">
  <div class="wordmark front-wordmark"><span class="wordmark-dot"></span>TumbleTrips</div>

  <div class="specialties">
    <p class="specialties-title">Specializing in</p>
    <ul>
      <li style="--bullet:var(--blue)">Glimmerland destinations</li>
      <li style="--bullet:var(--teal)">Pelican Bay Fun Park</li>
      <li style="--bullet:var(--green)">Cruises</li>
      <li style="--bullet:var(--orange)">All-Inclusive Vacations</li>
    </ul>
  </div>

  <div class="agent">
    <p class="agent-name">Marla Quint</p>
    <p class="agent-role">OWNER</p>
  </div>

  <ul class="contacts">
    <li><svg viewBox="0 0 16 16"><rect x="4" y="1" width="8" height="14" rx="1.5" fill="none" stroke="var(--blue)" stroke-width="1.6"/><circle cx="8" cy="12.5" r=".9" fill="var(--blue)"/></svg>555-218-4603</li>
    <li><svg viewBox="0 0 16 16"><path d="M3 1.5l3 .5 1 3.5-1.8 1.3a9 9 0 0 0 4 4L10.5 9l3.5 1 .5 3-2 1.5C7 14 2 9 1.5 3.5z" fill="var(--teal)"/></svg>555-647-1925</li>
    <li><svg viewBox="0 0 16 16"><rect x="1" y="3" width="14" height="10" fill="none" stroke="var(--green)" stroke-width="1.6"/><path d="M1 3l7 6 7-6" fill="none" stroke="var(--green)" stroke-width="1.6"/></svg>Marla@TumbleTrips.example</li>
    <li><svg viewBox="0 0 16 16" fill="none" stroke="var(--orange)" stroke-width="1.4"><circle cx="8" cy="8" r="6.5"/><ellipse cx="8" cy="8" rx="3" ry="6.5"/><path d="M1.5 8h13"/></svg>www.TumbleTrips.example</li>
  </ul>

  <div class="social"><span class="social-mark"></span>TumbleTrips</div>

  <div class="color-band">
    <span class="band-blue"></span><span class="band-teal"></span><span class="band-green"></span><span class="band-yellow"></span><span class="band-orange"></span>
  </div>
</section>

</body>
</html>
```